KRT Flyer to attract applicants 11x17

Lantern Stagehand Collective provides crew for local concerts, filming, theater, and corporate events.
The flyer will be posted on bulletin boards at colleges with theater programs.
Our primary venues are historic theaters in downtown LA
Need a 11x17 poster to attract potential applicants/crew
I have attached a poster that one of our staff made that has all if the relevant info - but i know the poster can look much better than that. I have also attached many images and our logo. It is not necessary to use all of the images, or any of them. The two images of the theater interiors are the venues we operate so they would be the first to include. I can send additional info or images upon request. Thank you

Industry/Entity Type

Entertainment

Requirements
Must have
• APPLY@KRTCREW.EXAMPLE

```html
<!DOCTYPE html>
<html lang="en">
<head>
<meta charset="utf-8">
<title>Lantern Stagehand Collective – Open Positions</title>
<link href="https://fonts.googleapis.com/css2?family=Kanit:wght@300;500;700;800&family=Poppins:wght@300;500;600;700&display=swap" rel="stylesheet">
<style>
  :root {
    --page-bg: #e2e2e2;
    --blue-top: #2356a8;
    --blue-mid: #2e3192;
    --indigo: #2b2f8c;
    --yellow: #ffcc00;
    --white: #ffffff;
    --ink: #111111;
    --red: #c8203a;
  }
  * { margin: 0; padding: 0; box-sizing: border-box; }
  html, body {
    width: 1200px; height: 1200px; overflow: hidden;
    background: var(--page-bg);
  }
  .poster {
    position: absolute; left: 212px; top: 0;
    width: 776px; height: 1200px; overflow: hidden;
    background: linear-gradient(180deg, var(--blue-top) 0%, var(--blue-mid) 45%, var(--indigo) 100%);
  }
  .poster-art { position: absolute; inset: 0; width: 776px; height: 1200px; }
  .brand {
    position: absolute; left: 158px; top: 53px;
    display: flex; align-items: center; gap: 20px;
  }
  .brand-dot {
    width: 104px; height: 104px; border-radius: 50%;
    border: 10px solid var(--white);
  }
  .brand-name {
    font-family: "Kanit", sans-serif; font-weight: 500;
    color: var(--white); line-height: 1.05; text-transform: uppercase;
  }
  .brand-name .line-1 { display: block; font-size: 33px; letter-spacing: 0.5px; }
  .brand-name .line-2 { display: block; font-size: 19px; letter-spacing: 12px; margin-top: 4px; }
  .headline {
    position: absolute; left: 0; width: 100%; top: 222px;
    text-align: center; font-family: "Kanit", sans-serif; font-weight: 800;
    font-size: 84px; line-height: 1; letter-spacing: -2px; color: var(--yellow);
  }
  .headline-rule {
    position: absolute; left: 204px; top: 309px; width: 371px; height: 3px;
    background: var(--yellow);
  }
  .intro {
    position: absolute; left: 0; width: 100%; top: 364px;
    text-align: center; font-family: "Kanit", sans-serif; font-weight: 300;
    font-size: 45px; line-height: 1; color: var(--white);
  }
  .role {
    position: absolute; left: 0; width: 100%; top: 410px;
    text-align: center; font-family: "Kanit", sans-serif; font-weight: 700;
    font-size: 52px; line-height: 1; color: var(--yellow);
  }
  .roster {
    position: absolute; left: 0; width: 100%; top: 492px;
    text-align: center; font-family: "Poppins", sans-serif; font-weight: 300;
    font-size: 31px; line-height: 40px; color: var(--white);
  }
  .apply-label {
    position: absolute; left: 0; width: 100%; top: 998px;
    text-align: center; font-family: "Poppins", sans-serif; font-weight: 500;
    font-size: 23px; color: var(--white);
  }
  .apply-email {
    position: absolute; left: 193px; top: 1033px; width: 390px; height: 52px;
    border-radius: 14px; background: var(--yellow);
    box-shadow: 0 3px 6px rgba(0,0,0,0.3);
    display: flex; align-items: center; justify-content: center;
    font-family: "Poppins", sans-serif; font-weight: 600; font-size: 23px;
    color: var(--ink);
  }
  .website {
    position: absolute; left: 0; width: 100%; top: 1134px;
    display: flex; align-items: center; gap: 18px;
  }
  .website-rule { flex: 1; height: 2px; background: var(--white); }
  .website-text {
    font-family: "Poppins", sans-serif; font-weight: 600; font-size: 16px;
    letter-spacing: 8px; color: var(--white); text-transform: uppercase;
    margin-right: -8px;
  }
</style>
</head>
<body>
<main class="poster">
  <svg class="poster-art" viewBox="0 0 1115 1724" preserveAspectRatio="none" aria-hidden="false">
    <defs>
      <linearGradient id="skyline-fill" x1="0" y1="0" x2="0" y2="1">
        <stop offset="0" stop-color="#8a2a5a"/>
        <stop offset="0.5" stop-color="#4b3090"/>
        <stop offset="1" stop-color="#2d3590"/>
      </linearGradient>
      <radialGradient id="red-glow" cx="0" cy="0.2" r="0.8">
        <stop offset="0" stop-color="#d4213a"/>
        <stop offset="1" stop-color="#d4213a" stop-opacity="0"/>
      </radialGradient>
      <linearGradient id="left-venue" x1="0" y1="0" x2="1" y2="1">
        <stop offset="0" stop-color="#6a2a5c"/>
        <stop offset="0.45" stop-color="#b8604a"/>
        <stop offset="1" stop-color="#3a2a6e"/>
      </linearGradient>
      <linearGradient id="right-venue" x1="0" y1="0" x2="1" y2="1">
        <stop offset="0" stop-color="#c88a3a"/>
        <stop offset="0.5" stop-color="#9a5a22"/>
        <stop offset="1" stop-color="#5a2a1a"/>
      </linearGradient>
    </defs>

    <g role="img" aria-label="Blurred night skyline of downtown Los Angeles">
      <rect x="0" y="1200" width="1115" height="524" fill="url(#skyline-fill)"/>
      <rect x="0" y="1200" width="1115" height="524" fill="url(#red-glow)"/>
    </g>

    <path class="swoosh" d="M0,1180 C170,1300 380,1380 650,1262 L660,1280 C390,1420 160,1360 0,1250 Z" fill="#ffffff"/>
    <path class="swoosh" d="M515,1030 C610,1170 700,1360 1115,1405 L1115,1460 C690,1430 580,1250 515,1030 Z" fill="#ffffff"/>

    <path role="img" aria-label="Photo of an ornate historic theater auditorium with domed ceiling and stage"
          d="M0,866 C190,850 420,890 530,1040 C575,1110 605,1195 645,1262 C400,1375 180,1300 0,1180 Z"
          fill="url(#left-venue)"/>
    <path role="img" aria-label="Photo of a gilded historic theater interior with balconies and boxes"
          d="M530,1036 C700,880 900,860 1115,738 L1115,1400 C780,1370 650,1200 530,1036 Z"
          fill="url(#right-venue)"/>
  </svg>

  <div class="brand">
    <span class="brand-dot"></span>
    <span class="brand-name"><span class="line-1">Lantern Stagehand</span><span class="line-2">Collective</span></span>
  </div>

  <h1 class="headline">OPEN POSITIONS</h1>
  <div class="headline-rule"></div>

  <p class="intro">WE ARE LOOKING FOR</p>
  <p class="role">TALENTED TECHNICIANS</p>
  <p class="roster">TO ADD TO OUR ROSTER OF<br>SKILLED PROFESSIONALS</p>

  <p class="apply-label">Send Resume to:</p>
  <p class="apply-email">APPLY@KRTCREW.EXAMPLE</p>

  <div class="website">
    <span class="website-rule"></span>
    <span class="website-text">www.krtcrew.example</span>
    <span class="website-rule"></span>
  </div>
</main>
</body>
</html>
```